47 on Birch Apartment Mailer to Competition

I need a postcard mailer designed that will be promoting a new apartment building in downtown Rochester NY. The postcards are being mailed to other apartment communities the we are in direct competition with. I have enclosed a bunch of info to guide you.

Target Market(s)

Other communities in the market

Industry/Entity Type

Property Management

Requirements
Must have
• Exterior rendering, features. Fit standard postcard, colors similar to enclosed, grey, white coral
Nice to have
• Interior Pictures

```html
<!DOCTYPE html>
<html lang="en">
<head>
<meta charset="utf-8">
<title>47 on Birch – Postcard Mailer</title>
<link href="https://fonts.googleapis.com/css2?family=Fira+Sans+Condensed:wght@400;700&display=swap" rel="stylesheet">
<style>
  :root {
    --maroon: #5c1d1a;
    --maroon-deep: #3f1311;
    --coral: #e8553f;
    --coral-soft: rgba(232, 85, 63, 0.85);
    --white: #ffffff;
    --ink: #2a2422;
    --sky-top: #6f8fae;
    --sky-mid: #c9c4bd;
    --sky-warm: #e6a46f;
  }
  * { margin: 0; padding: 0; box-sizing: border-box; }
  html, body { width: 850px; height: 1200px; overflow: hidden; background: #fff; }
  body { font-family: "Fira Sans Condensed", "Arial Narrow", sans-serif; color: var(--white); }
  .mailer { position: relative; width: 850px; height: 1200px; overflow: hidden; }

  .hero-photo {
    position: absolute; inset: 0 0 auto 0; height: 780px;
    background:
      linear-gradient(90deg, rgba(0,0,0,0) 52%, rgba(205,212,220,0.55) 54%, rgba(190,198,208,0.7) 100%),
      linear-gradient(180deg, var(--sky-top) 0%, var(--sky-mid) 30%, var(--sky-warm) 45%, #7d7a76 65%, #4a4642 100%);
  }
  .interior-photo {
    position: absolute; left: 0; top: 620px; width: 850px; height: 520px;
    background: linear-gradient(180deg, #6b625c 0%, #3d3532 100%);
  }
  .panels { position: absolute; inset: 0; }

  .brand-badge {
    position: absolute; left: -96px; top: -120px; width: 416px; height: 416px;
    border-radius: 50%; background: var(--white);
    border: 6px solid var(--maroon);
    box-shadow: 4px 4px 0 0 var(--coral);
  }
  .brand-name {
    position: absolute; left: 0; top: 186px; width: 290px; text-align: center;
    font-size: 36px; font-weight: 700; letter-spacing: 1px; color: var(--maroon);
  }
  .brand-mark {
    position: absolute; left: 120px; top: 60px; width: 50px; height: 50px;
    background: var(--maroon);
  }

  .floor-plans {
    position: absolute; left: 0; top: 356px; width: 292px; height: 210px;
    background: var(--coral-soft); padding: 16px 0 0 35px;
  }
  .floor-plans h2 { font-size: 29px; font-weight: 700; line-height: 1.05; margin-bottom: 6px; }
  .floor-plans p { font-size: 22px; line-height: 30px; white-space: nowrap; }

  .feature-col { position: absolute; top: 694px; width: 425px; text-align: center; }
  .feature-col.community { left: 0; }
  .feature-col.home { left: 425px; }
  .feature-col h2 { font-size: 31px; font-weight: 700; margin-bottom: 10px; }
  .feature-col li { list-style: none; font-size: 22px; line-height: 33.3px; }
  .feature-col li.wrap { line-height: 25px; margin-bottom: 8px; }

  .contact-bar {
    position: absolute; left: 0; top: 1124px; width: 850px; height: 76px;
    display: flex; justify-content: center; align-items: center; gap: 26px;
    color: var(--ink); font-size: 25px; padding-top: 4px;
  }
  .contact-bar .divider { width: 3px; height: 30px; background: var(--ink); }
</style>
</head>
<body>
<main class="mailer">
  <div class="hero-photo" role="img" aria-label="Exterior rendering of the glass-fronted apartment tower at dusk on a downtown street"></div>
  <div class="interior-photo" role="img" aria-label="Interior photo of an apartment kitchen with granite countertop and sink"></div>

  <svg class="panels" width="850" height="1200" viewBox="0 0 850 1200" aria-hidden="true">
    <defs>
      <clipPath id="panel-shape">
        <path d="M0,722 Q560,560 850,690 L850,1124 L0,1124 Z"/>
      </clipPath>
    </defs>
    <g clip-path="url(#panel-shape)">
      <rect x="0" y="540" width="425" height="600" fill="var(--maroon)" opacity="0.82"/>
      <rect x="425" y="540" width="425" height="600" fill="var(--coral)" opacity="0.9"/>
    </g>
    <path d="M0,722 Q560,560 850,690" fill="none" stroke="var(--white)" stroke-width="9"/>
    <polygon points="0,1124 850,1124 850,1200 0,1200" fill="var(--white)"/>
    <polygon points="0,1124 30,1124 0,1160" fill="var(--maroon-deep)"/>
    <polygon points="850,1124 820,1124 850,1160" fill="var(--coral)"/>
  </svg>

  <div class="brand-badge">
    <div class="brand-mark" style="left:218px;top:150px;"></div>
  </div>
  <div class="brand-name">47 ON BIRCH</div>

  <section class="floor-plans">
    <h2>FLOOR PLANS</h2>
    <p>1 Bedroom</p>
    <p>1 Bedroom with Den</p>
    <p>and 2 Bedroom 2 Bath Available</p>
    <p>$1400 to $3300</p>
    <p>&nbsp;775 to 1677 sq. ft.</p>
  </section>

  <section class="feature-col community">
    <h2>COMMUNITY FEATURES</h2>
    <ul>
      <li>Rooftop patio</li>
      <li>24 Hour Fitness</li>
      <li>5x10 Storage Unit</li>
      <li>High Speed Internet and cable Included</li>
      <li>Heat and A/C Included</li>
      <li>Parking Available, One Spot Included</li>
      <li class="wrap">Modern Security with Controlled Access<br>and key Fobs</li>
      <li>Amazing Views</li>
      <li>Den Available</li>
      <li>24 Hour Maintenance</li>
    </ul>
  </section>

  <section class="feature-col home">
    <h2>HOME FEATURES</h2>
    <ul>
      <li>Floor to Ceiling Operable Windows</li>
      <li>W/D In Unit</li>
      <li>LED Lighting</li>
      <li>Hardwood Flooring</li>
      <li>Automatic Window Treatments</li>
      <li>Granite Countertops</li>
      <li>Undermount Sinks</li>
      <li>Tile backsplash</li>
      <li>Walk-In Closets Available</li>
      <li>Open Floor Plans</li>
      <li>Contemporary Cabinetry and Fixtures</li>
    </ul>
  </section>

  <footer class="contact-bar">
    <span>585.555.0147</span>
    <span class="divider"></span>
    <span>LEASING@47ONBIRCH.COM</span>
    <span class="divider"></span>
    <span>WWW.47ONBIRCH.COM</span>
  </footer>
</main>
</body>
</html>
```